Oil Field Service company needs professional business cards

Looking to clean up our current company business cards and look a little more professional. Brenwick Casing Services is a US based company that services the oil field. We deal with engineers, managers and oil rigs....................................................................................................................................................................................................................................................................................................................................................................................................

Target Market(s)

Oil and Gas professionals

Industry/Entity Type

Oil And Gas

Contact Information for Business Card

See attached photo as example

Font styles to use
Sans Serif

Colors
ec1f27

Requirements
Must have
• Company Logo, Name, Title, Cell, Office, Fax, Email.
• See attached photo
Nice to have
• External CRT, Internal CRT, Casing Crews, Torque Turn, Laydown Machine
Should not have
• Do not introduce any new pictures and keep it professional looking

```html
<!DOCTYPE html>
<html lang="en">
<head>
<meta charset="utf-8">
<title>Brenwick Casing Services – Business Card</title>
<link rel="stylesheet" href="https://fonts.googleapis.com/css2?family=Oswald:wght@500&family=Roboto:wght@400;700&display=swap">
<style>
  :root {
    --brand-red: #d0211f;
    --brand-red-deep: #c01d1c;
    --slate: #3e5263;
    --paper: #f4f4f4;
    --ink: #2f3338;
    --ink-soft: #4a4f55;
    --backdrop: #e2e2e2;
    --white: #ffffff;
  }
  * { box-sizing: border-box; margin: 0; padding: 0; }
  html, body { width: 1200px; height: 576px; overflow: hidden; }
  body {
    background: var(--backdrop);
    font-family: "Roboto", Arial, sans-serif;
    position: relative;
  }
  .card {
    position: absolute;
    top: 138px;
    width: 484px;
    height: 294px;
    border-radius: 6px;
    overflow: hidden;
    box-shadow: 0 2px 5px rgba(0,0,0,0.22);
  }
  .card--front {
    left: 82px;
    background: linear-gradient(180deg, var(--brand-red) 0%, var(--brand-red-deep) 100%);
    display: flex;
    flex-direction: column;
    align-items: center;
    justify-content: center;
  }
  .wordmark {
    font-family: "Roboto", Arial, sans-serif;
    font-weight: 700;
    color: var(--white);
    text-transform: uppercase;
    text-align: center;
    letter-spacing: 2px;
  }
  .card--front .wordmark { font-size: 30px; line-height: 1.25; }
  .card--back {
    left: 602px;
    background: var(--paper);
  }
  .card__panel {
    position: absolute;
    left: 0; top: 0;
    width: 220px; height: 294px;
  }
  .card__panel-mark {
    position: absolute;
    left: 90px; top: 147px;
    width: 260px;
    transform: translate(-50%, -50%) rotate(-90deg);
  }
  .card__panel-mark .wordmark { font-size: 22px; line-height: 1.3; }
  .holder {
    position: absolute;
    right: 28px; top: 26px;
    text-align: right;
  }
  .holder__name {
    font-family: "Oswald", Arial, sans-serif;
    font-weight: 500;
    font-size: 22px;
    color: var(--ink);
    line-height: 1.1;
  }
  .holder__title {
    font-size: 11px;
    color: var(--ink-soft);
    margin-top: 2px;
  }
  .contact {
    position: absolute;
    right: 30px; top: 175px;
    list-style: none;
  }
  .contact__item {
    display: flex;
    justify-content: flex-end;
    align-items: center;
    height: 16.2px;
    font-size: 11.2px;
    color: var(--ink);
  }
  .contact__icon {
    width: 10px; height: 10px;
    margin-left: 9px;
    fill: var(--brand-red);
    flex: none;
  }
</style>
</head>
<body>

<section class="card card--front" aria-label="Business card front">
  <p class="wordmark">Brenwick<br>Casing Services</p>
</section>

<section class="card card--back" aria-label="Business card back">
  <svg class="card__panel" viewBox="0 0 220 294" aria-hidden="true">
    <path d="M0 0 H190 C208 80 214 200 174 294 H0 Z" fill="var(--brand-red)"/>
    <path d="M0 0 H182 C198 80 204 200 165 294 H0 Z" fill="var(--slate)"/>
  </svg>
  <div class="card__panel-mark">
    <p class="wordmark">Brenwick<br>Casing Services</p>
  </div>

  <header class="holder">
    <h1 class="holder__name">Cody Harwell</h1>
    <p class="holder__title">Area Manager</p>
  </header>

  <ul class="contact">
    <li class="contact__item">(580) 555-0142
      <svg class="contact__icon" viewBox="0 0 10 10" aria-label="Cell"><path d="M2 0.5 L3.6 2.6 L2.8 3.6 C3.4 5 4.8 6.5 6.4 7.2 L7.4 6.4 L9.5 8 L8.5 9.5 C4.5 9.4 0.6 5.5 0.5 1.5 Z"/></svg>
    </li>
    <li class="contact__item">(580) 555-0187
      <svg class="contact__icon" viewBox="0 0 10 10" aria-label="Office"><path d="M0.5 3.5 C2 1.5 8 1.5 9.5 3.5 L9.5 4.6 L7.4 4.6 L7.4 3.8 L2.6 3.8 L2.6 4.6 L0.5 4.6 Z M2 5.2 H8 L9 9 H1 Z"/></svg>
    </li>
    <li class="contact__item">(580) 555-0163
      <svg class="contact__icon" viewBox="0 0 10 10" aria-label="Fax"><path d="M2.5 0.5 H7.5 V3 H2.5 Z M0.5 3.6 H9.5 V7.5 H8 V6 H2 V7.5 H0.5 Z M2.6 6.6 H7.4 V9.5 H2.6 Z"/></svg>
    </li>
    <li class="contact__item">Fairmont, OK 73520
      <svg class="contact__icon" viewBox="0 0 10 10" aria-label="Address"><path d="M5 0.3 C2.9 0.3 1.5 1.9 1.5 3.8 C1.5 6.2 5 9.7 5 9.7 C5 9.7 8.5 6.2 8.5 3.8 C8.5 1.9 7.1 0.3 5 0.3 Z M5 2.4 A1.4 1.4 0 1 1 5 5.2 A1.4 1.4 0 1 1 5 2.4 Z" fill-rule="evenodd"/></svg>
    </li>
    <li class="contact__item">codyharwell@brenwickcs.com
      <svg class="contact__icon" viewBox="0 0 10 10" aria-label="Email"><path d="M0.5 2 H9.5 L5 5.6 Z M0.5 3 L5 6.6 L9.5 3 V8 H0.5 Z"/></svg>
    </li>
    <li class="contact__item">www.brenwickcs.com
      <svg class="contact__icon" viewBox="0 0 10 10" aria-label="Website"><path d="M5 0.5 A4.5 4.5 0 1 0 5 9.5 A4.5 4.5 0 1 0 5 0.5 Z M5 1.5 C4 2.5 3.7 3.6 3.7 5 C3.7 6.4 4 7.5 5 8.5 C6 7.5 6.3 6.4 6.3 5 C6.3 3.6 6 2.5 5 1.5 Z M1.5 4.6 H8.5 V5.4 H1.5 Z" fill-rule="evenodd"/></svg>
    </li>
  </ul>
</section>

</body>
</html>
```